The 22 Rules and Traps of House Lending or the 22 things that will derail your transaction and how to prevent them.

I am looking to do a series of 4 to 5 e-books that should have a consistent format and theme

The first of these should be entitled, "The 22 Rules and Traps of House Lending" That is similar in style to the attached e-book.
The attached e-book is pretty much the style that I am looking for, The same format can be followed. I have attached a black and white head shot image for the head shot areas that appears on page two of the attached e-book. I have also attached my company logo.
Please feel free to use the same or similar colors in my logo for the lay-out of the e-book. However please do not feel limited to those colors. - Feel free to use your imagination.

The content can be found here.

http://www.fredtheloanfox.example/loan-advice.php

For the final “About” page of the e-book - Please entitle it… About Fred the Loan Fox.
The content for the last page can be found in the attached document - Owen Thistlewood bio2

The first page is where the creativity come in

Requirements
Must have
• Note that this project is for one e-book - However, once the designer and format is chosen the remainder of the projects will be launched

```html
<!DOCTYPE html>
<html lang="en">
<head>
<meta charset="utf-8">
<title>The 22 Rules and Traps of House Lending – Page 8</title>
<link href="https://fonts.googleapis.com/css2?family=Questrial&family=Jost:wght@300;400;700;800&family=Crimson+Pro:wght@600;700&display=swap" rel="stylesheet">
<style>
  :root{
    --navy:#1f3566;
    --blue:#2f5fae;
    --callout:#3b63b0;
    --red:#e2262b;
    --body:#2b2f3a;
    --paper:#ffffff;
  }
  *{box-sizing:border-box;margin:0;padding:0}
  html,body{width:900px;height:1200px;overflow:hidden;background:var(--paper)}
  .page{position:relative;width:900px;height:1200px;background:var(--paper);color:var(--body)}
  .tip{position:absolute;left:0;right:0}
  .tip-number{position:absolute;left:20px;width:44px;height:44px;border-radius:50%;
    background:var(--navy);color:#fff;font-family:"Crimson Pro",serif;font-weight:700;
    font-size:27px;line-height:44px;text-align:center}
  .tip-title{font-family:"Questrial",sans-serif;color:var(--navy);font-size:28px;line-height:36px;
    padding-left:64px;padding-right:40px;text-indent:42px;font-weight:400}
  .tip-title.flush{text-indent:42px}
  .tip-title .do{font-family:"Jost",sans-serif;font-weight:700;color:var(--blue)}
  .tip-title .dont{font-family:"Jost",sans-serif;font-weight:700;color:var(--red)}
  .tip-body{padding:0 70px 0 67px;font-family:"Jost",sans-serif;font-weight:300;font-size:15.2px;line-height:22.5px;color:var(--body)}
  .tip-body p{margin-top:14px}
  .tip-body .callout{font-weight:700;color:var(--callout);font-size:17.5px;line-height:28px;margin-top:18px}
  .footer{position:absolute;left:65px;right:60px;top:1108px;height:60px;display:flex;align-items:flex-end}
  .brand{display:flex;align-items:center;gap:6px;font-family:"Jost",sans-serif;font-weight:700;color:var(--navy);font-size:15px;height:44px;padding-right:10px;border-right:2px solid var(--navy)}
  .brand-mark{width:12px;height:12px;background:var(--navy)}
  .footer-title,.footer-licence{font-family:"Crimson Pro",serif;font-weight:600;color:var(--navy);font-variant:small-caps;font-size:16px;letter-spacing:.5px;padding-bottom:6px}
  .footer-title{margin-left:12px}
  .footer-title b{font-size:20px}
  .footer-licence{margin-left:auto;margin-right:110px}
  .page-number{position:absolute;right:0;bottom:8px;width:30px;height:30px;background:var(--navy);color:#fff;
    font-family:"Crimson Pro",serif;font-size:19px;line-height:30px;text-align:center}
</style>
</head>
<body>
<main class="page">

  <section class="tip" style="top:40px">
    <div class="tip-number" style="top:14px">16</div>
    <h2 class="tip-title"><span class="do">Do</span> remain employed during the loan process.</h2>
    <div class="tip-body">
      <p>Again, this one may seem incredibly obvious, but borrowers have been known to quit their jobs during the loan process without considering that their lack of employment would adversely affect the closing of their loan. They wrongly assume that, since they were already “in underwriting” or that their loan was al-ready “approved,” they were in no danger of a loan denial.</p>
      <p style="margin-top:22px">All mortgages are only conditionally approved until the day of closing, and part of the final approval process is a verbal verification of employment. On the day of closing the underwriter will call the borrower’s employer to confirm that the borrower is still employed. If the underwriter calls your employer and they cannot confirm your employment status, your loan will be put on hold until your em-ployment status can be determined.</p>
    </div>
  </section>

  <section class="tip" style="top:352px">
    <div class="tip-number" style="top:0">17</div>
    <h2 class="tip-title"><span class="dont">Don’t</span> take a voluntary leave of absence, a cut in salary or go on maternity leave while going through the underwriting process.</h2>
    <div class="tip-body">
      <p style="margin-top:16px">Sometimes borrowers mistakenly assume that a leave of absence or other un-paid leave is still acceptable to a lender during underwriting because their job is still intact during the leave.</p>
      <p class="callout">If the borrower is not earning income on the day of funding then the loan will not be closed for the same reasons mentioned above.</p>
    </div>
  </section>

  <section class="tip" style="top:630px">
    <div class="tip-number" style="top:0">18</div>
    <h2 class="tip-title"><span class="do">Do</span> inform your mortgage professional of any real estate that you own either solely or jointly that is not mortgaged.</h2>
    <div class="tip-body">
      <p style="margin-top:16px">It’s very important that your mortgage professional know about any properties that you own, either solely or jointly, even if those properties are not mortgaged. These properties may be second homes, vacation homes, co-ops or time sharing properties.</p>
      <p class="callout">Even though you may not have mortgages on a property, you may still have ob-ligations for property taxes, hazard insurance and/or homeowner’s association dues. These payment will have to be calculated into your debt-to-income ratio.</p>
      <p style="margin-top:18px">As mentioned previously, if your loan is at the edge of the lender’s allowable debt-to-income ratio, the extra monthly funds required to service property taxes, hazard insurance and or homeowners dues could adversely affect your debt-to-income ratio just enough to result in a loan denial. It is better to disclose all owned properties up front in order to ensure that your mortgage professional is able to properly structure your loan.</p>
    </div>
  </section>

  <footer class="footer">
    <div class="brand"><span class="brand-mark"></span>Harborline Home Loans</div>
    <div class="footer-title">The <b>22</b> Rules and Traps of House Lending</div>
    <div class="footer-licence">Licence MLO#40718</div>
    <div class="page-number">8</div>
  </footer>

</main>
</body>
</html>
```